Home Health Company Needs a Corporate Identity Package

We need a corporate identity package (see what it should include below) for a home health care company. The design should be professional, uncluttered, simple and created in Publisher (so that we can edit the design in the future, if necessary. )
We need the following created:
-Presentation folder
-Business card template (color, double sided)
-Letterhead
-Stationary
-postcard sized marketing piece (5.5" x 8.5", color, double sided)

Target Market(s)

We are in the business of supplying personal care aids for in home care. Our services are directed towards older, retired individuals with some disability or illness. However, we will be marketing to the children or relatives of our in home clients. We want our logo to emphasize our reliability and personalized services.

Industry/Entity Type

Home Health Care

Requirements
Must have
• The design should be professional, uncluttered, simple and created in Publisher (so that we can edit the design in the future, if necessary. )

```html
<!DOCTYPE html>
<html lang="en">
<head>
<meta charset="utf-8">
<title>Willow Home Health — Stationery Set</title>
<link rel="stylesheet" href="https://fonts.googleapis.com/css2?family=Source+Sans+3:wght@400;600&family=Great+Vibes&display=swap">
<style>
  :root{
    --bg:#eceeef;
    --paper:#ffffff;
    --blue:#4cc6ef;
    --blue-soft:#74c6ea;
    --gray:#5f6266;
    --charcoal:#3e4043;
    --light-gray:#c9cacb;
  }
  *{box-sizing:border-box;margin:0;padding:0}
  html,body{width:1200px;height:1000px;overflow:hidden;background:var(--bg)}
  body{position:relative;font-family:"Source Sans 3",Arial,sans-serif;color:var(--gray)}
  .piece{position:absolute;background:var(--paper);overflow:hidden}

  .brand{position:absolute;display:flex;align-items:center;gap:.35em;color:var(--blue);font-weight:600;line-height:.92;letter-spacing:-.01em}
  .brand__dot{width:1.3em;height:1.3em;border-radius:50%;background:var(--blue);flex:none}
  .brand__name span{display:block}

  .band{position:absolute;left:0;right:0;background:var(--blue);border-top:3px solid var(--gray);display:flex;align-items:center;color:#fff;font-size:5px;line-height:1.3}
  .band__col{padding:0 10px;border-left:1px solid rgba(255,255,255,.8)}
  .band__col:first-child{border-left:none}
  .band__dot{width:12px;height:12px;border-radius:50%;background:rgba(255,255,255,.85);margin:0 14px 0 12px}

  /* letterhead */
  .letterhead{left:290px;top:96px;width:268px;height:420px}
  .letterhead .brand{right:16px;top:30px;font-size:21px}
  .letterhead .band{bottom:0;height:27px}

  /* folder */
  .folder{left:635px;top:78px;width:350px;height:440px}
  .folder .brand{right:16px;top:14px;font-size:29px}
  .folder__rule{position:absolute;left:0;right:0;top:174px;height:11px;background:var(--gray)}
  .folder__panel{position:absolute;left:0;right:0;top:185px;bottom:10px;background:var(--blue)}
  .folder__foot{position:absolute;left:0;right:0;bottom:0;height:10px;background:var(--gray)}
  .ghost-circle{position:absolute;border-radius:50%;background:rgba(255,255,255,.25)}
  .folder .ghost-circle{left:80px;top:28px;width:190px;height:190px}

  /* business cards */
  .card{width:138px;height:84px}
  .card--front{left:183px;top:548px}
  .card--front .brand{left:10px;top:11px;font-size:9px}
  .card--front .card__circle{position:absolute;right:-30px;top:4px;width:70px;height:70px;border-radius:50%;border:8px solid var(--light-gray)}
  .card__person{position:absolute;left:12px;top:46px;font-size:5px;color:var(--blue);line-height:1.4}
  .card__person span{display:block;color:var(--gray)}
  .card--front .band{bottom:0;height:18px;font-size:4px}
  .card--front .band__col{padding:0 4px}
  .card--back{left:183px;top:645px;height:80px;background:var(--charcoal)}
  .card--back .brand{left:18px;top:18px;font-size:14px}
  .card--back .card__circle{position:absolute;right:-34px;top:2px;width:76px;height:76px;border-radius:50%;border:9px solid #5a5c60}

  /* envelope front */
  .envelope{left:352px;top:562px;width:330px;height:160px}
  .envelope .brand{left:18px;top:12px;font-size:24px}
  .envelope .band{bottom:0;height:24px;font-size:6.5px;justify-content:space-between}
  .envelope .band__col{border:none;padding-left:10px}

  /* envelope back */
  .envelope-back{left:710px;top:562px;width:332px;height:160px}
  .envelope-back svg{position:absolute;left:0;top:0}

  /* postcard */
  .postcard{left:242px;top:772px;width:198px;height:182px}
  .postcard .brand{left:48px;top:8px;font-size:17px}
  .postcard__rule{position:absolute;left:0;right:0;top:60px;height:9px;background:var(--gray)}
  .postcard__panel{position:absolute;left:0;right:0;top:69px;bottom:0;background:var(--blue-soft)}
  .postcard .ghost-circle{left:48px;top:20px;width:92px;height:92px}

  /* disc */
  .disc{position:absolute;left:470px;top:790px;width:136px;height:136px;border-radius:50%;background:#f4f5f6;border:2px solid var(--gray)}
  .disc .brand{left:40px;top:6px;font-size:12px}
  .disc__hub{position:absolute;left:44px;top:44px;width:44px;height:44px;border-radius:50%;background:#d9dadb;border:1px solid #b8b9bb}
  .disc__hole{position:absolute;left:13px;top:13px;width:16px;height:16px;border-radius:50%;background:var(--bg);border:1px solid #b8b9bb}

  /* compliment slip */
  .slip{left:742px;top:772px;width:300px;height:144px}
  .slip .brand{left:20px;top:20px;font-size:23px}
  .slip__note{position:absolute;right:16px;top:106px;font-family:"Great Vibes",cursive;font-size:13px;color:var(--charcoal)}
  .slip__note em{font-style:normal;color:var(--blue)}
  .slip .band{bottom:0;height:18px}
</style>
</head>
<body>

<section class="piece letterhead">
  <div class="brand"><span class="brand__dot"></span><div class="brand__name"><span>Willow</span><span>Home</span><span>Health</span></div></div>
  <footer class="band">
    <span class="band__dot"></span>
    <div class="band__col">street name, city name,<br>state zip code</div>
    <div class="band__col">Phone: 555-555-5555<br>Fax: 555-555-5555</div>
    <div class="band__col">info@website.com<br>www.website.com</div>
  </footer>
</section>

<section class="piece folder">
  <div class="brand"><span class="brand__dot"></span><div class="brand__name"><span>Willow</span><span>Home</span><span>Health</span></div></div>
  <div class="folder__rule"></div>
  <div class="folder__panel"><span class="ghost-circle"></span></div>
  <div class="folder__foot"></div>
</section>

<section class="piece card card--front">
  <div class="brand"><span class="brand__dot"></span><div class="brand__name"><span>Willow</span><span>Home</span><span>Health</span></div></div>
  <span class="card__circle"></span>
  <div class="card__person">Employee name<span>Title</span></div>
  <footer class="band">
    <div class="band__col">street name, city name,<br>state zip code</div>
    <div class="band__col">Phone: 555-555-5555<br>Fax: 555-555-5555</div>
    <div class="band__col">info@website.com<br>www.website.com</div>
  </footer>
</section>

<section class="piece card card--back">
  <div class="brand"><span class="brand__dot"></span><div class="brand__name"><span>Willow</span><span>Home</span><span>Health</span></div></div>
  <span class="card__circle"></span>
</section>

<section class="piece envelope">
  <div class="brand"><span class="brand__dot"></span><div class="brand__name"><span>Willow</span><span>Home</span><span>Health</span></div></div>
  <footer class="band">
    <div class="band__col">Suite 210, 48 Orchard Row, Fairhaven 20415</div>
    <span class="band__dot"></span>
  </footer>
</section>

<section class="piece envelope-back">
  <svg width="332" height="160" viewBox="0 0 332 160">
    <path d="M0 0H332V40Q332 52 318 52H178Q166 52 166 62Q166 52 154 52H14Q0 52 0 40Z" fill="var(--blue)"/>
    <circle cx="166" cy="24" r="11" fill="#fff"/>
  </svg>
</section>

<section class="piece postcard">
  <div class="brand"><span class="brand__dot"></span><div class="brand__name"><span>Willow</span><span>Home</span><span>Health</span></div></div>
  <div class="postcard__rule"></div>
  <div class="postcard__panel"><span class="ghost-circle"></span></div>
</section>

<section class="disc">
  <div class="brand"><span class="brand__dot"></span><div class="brand__name"><span>Willow</span><span>Home</span><span>Health</span></div></div>
  <div class="disc__hub"><span class="disc__hole"></span></div>
</section>

<section class="piece slip">
  <div class="brand"><span class="brand__dot"></span><div class="brand__name"><span>Willow</span><span>Home</span><span>Health</span></div></div>
  <p class="slip__note"><em>With</em> Compliments</p>
  <footer class="band">
    <div class="band__col">street name, city name,<br>state zip code</div>
    <div class="band__col">Phone: 555-555-5555<br>Fax: 555-555-5555</div>
    <div class="band__col">info@website.com<br>www.website.com</div>
    <span class="band__dot"></span>
  </footer>
</section>

</body>
</html>
```